Business Cards, Letterhead, Envelopes etc.
Need design that fits with tech saavy customers
Business Cards, Letterhead, Envelopes etc.  -
Creative Brief
Use specific fonts
Use same font or one that works with the logo
Cutting-Edge
Dean R. Marlow
President
418 Bellwick Street Palo Alto, CA 94306
dean@quevrafin.com
quevrafin.com
CA DRE: #00471362, NMLS: #517294
Need design for business cards, letterhead, #10 envelopes and mailing labels for package shipments.

```html
<!DOCTYPE html>
<html lang="en">
<head>
<meta charset="utf-8">
<title>Quevrafin Stationery</title>
<link rel="stylesheet" href="https://fonts.googleapis.com/css2?family=Montserrat:wght@500;600;700&family=Tinos:wght@400;700&display=swap">
<style>
  :root {
    --bg: #8e8e8e;
    --paper: #ffffff;
    --brand-blue: #1f4f9c;
    --brand-green: #6aac3c;
    --ink: #2b2b2b;
    --muted: #6b6b6b;
    --sign: #d9dee8;
    --shadow: rgba(0,0,0,0.25);
  }
  * { box-sizing: border-box; margin: 0; padding: 0; }
  html, body { width: 1200px; height: 626px; overflow: hidden; background: var(--bg); }
  .canvas { position: relative; width: 1200px; height: 626px; background: var(--bg); font-family: "Montserrat", sans-serif; color: var(--ink); }
  .sheet { position: absolute; background: var(--paper); box-shadow: 0 1px 4px var(--shadow); overflow: hidden; }
  .band { position: absolute; left: 0; bottom: 0; width: 100%; background: linear-gradient(180deg, rgba(106,172,60,0.55) 0%, rgba(31,79,156,0.75) 55%, var(--brand-blue) 100%); }
  .wordmark { font-family: "Montserrat", sans-serif; font-weight: 700; color: var(--brand-blue); letter-spacing: 0.02em; line-height: 1; }
  .small { font-family: "Montserrat", sans-serif; font-weight: 500; color: var(--muted); }

  /* Business card */
  .card { left: 29px; top: 307px; width: 182px; height: 113px; }
  .card__person { position: absolute; top: 12px; width: 100%; text-align: center; font-size: 5px; line-height: 7px; }
  .card__person strong { color: var(--ink); font-weight: 600; }
  .card .wordmark { position: absolute; top: 36px; width: 100%; text-align: center; font-size: 17px; }
  .card .band { height: 24px; }

  /* Letterhead */
  .letterhead { left: 264px; top: 24px; width: 528px; height: 593px; }
  .letterhead .wordmark { position: absolute; left: 34px; top: 30px; font-size: 24px; }
  .letterhead__contact { position: absolute; right: 30px; top: 20px; text-align: right; font-size: 5px; line-height: 7px; }
  .letter { position: absolute; left: 34px; top: 86px; width: 460px; font-family: "Tinos", serif; font-size: 7.5px; line-height: 10px; color: var(--ink); }
  .letter__opening { font-weight: 700; font-size: 8.5px; line-height: 11px; margin-bottom: 14px; }
  .letter p { margin-bottom: 10px; text-align: justify; }
  .letter__signature { width: 96px; height: 36px; background: var(--sign); margin: 6px 0 6px; }
  .letterhead .band { height: 46px; }

  /* Envelope back */
  .envelope-back { left: 816px; top: 24px; width: 365px; height: 187px; }
  .envelope-back .flap { position: absolute; left: 0; top: 0; width: 100%; height: 124px; display: block; }
  .envelope-back .flap .blue { fill: var(--brand-blue); }

  /* Envelope front */
  .envelope-front { left: 816px; top: 329px; width: 365px; height: 247px; }
  .envelope-front .wordmark { position: absolute; left: 22px; top: 92px; font-size: 20px; }
  .envelope-front__return { position: absolute; right: 22px; top: 20px; text-align: right; font-size: 5px; line-height: 7px; }
  .envelope-front .band { height: 42px; }
</style>
</head>
<body>
<div class="canvas">

  <section class="sheet card" aria-label="Business card">
    <div class="card__person small"><strong>Dean R. Marlow</strong><br>President<br>dean@quevrafin.com</div>
    <div class="wordmark">QUEVRAFIN</div>
    <div class="band" role="img" aria-label="Decorative blue and green band"></div>
  </section>

  <section class="sheet letterhead" aria-label="Letterhead">
    <div class="wordmark">QUEVRAFIN</div>
    <div class="letterhead__contact small">
      418 Bellwick Street<br>Palo Alto, CA 94306<br>dean@quevrafin.com<br>quevrafin.com<br>CA DRE: #00471362, NMLS: #517294
    </div>
    <div class="letter">
      <div class="letter__opening">Lorem ipsum<br>dolor sit amet<br>consectetuer adipiscing elit</div>
      <p>Thank you for choosing us for your home financing needs. Our team reviews every file with care, keeps you informed at each step, and works to close your loan on schedule. We value the trust you place in us and look forward to serving you.</p>
      <p>Enclosed you will find a summary of your current rate options, estimated closing costs and the documents we still need. Please review each item and return the signed forms at your convenience so we can move your application forward without delay.</p>
      <p>Our online portal lets you upload files, track progress and message your loan officer from any device. If you have questions about terms, timelines or next steps, our staff is available by email throughout the week.</p>
      <p>Once your appraisal is complete, we will confirm the final figures with you and schedule a closing date that fits your plans. Our underwriters aim to respond to every condition within two business days, and we will let you know right away if anything else is required from you or your agent.</p>
      <p>We also offer guidance on refinancing, rate locks and first-time buyer programs. If friends or family are planning a purchase, we would be happy to help them explore their options with the same attention we give to every client.</p>
      <p>Thank you again for your business. We are glad to be part of your next move.</p>
      <div>Sincerely yours,</div>
      <div class="letter__signature" role="img" aria-label="Handwritten signature"></div>
      <div>Dean R. Marlow, President</div>
    </div>
    <div class="band" role="img" aria-label="Decorative blue and green band"></div>
  </section>

  <section class="sheet envelope-back" aria-label="Envelope back">
    <svg class="flap" viewBox="0 0 365 124" preserveAspectRatio="none" aria-hidden="true">
      <path class="blue" d="M0 0 L365 0 L365 18 L200 118 Q182 126 165 118 L0 18Z"/>
    </svg>
  </section>

  <section class="sheet envelope-front" aria-label="Envelope front">
    <div class="envelope-front__return small">
      418 Bellwick Street<br>Palo Alto, CA 94306<br>quevrafin.com
    </div>
    <div class="wordmark">QUEVRAFIN</div>
    <div class="band" role="img" aria-label="Decorative blue and green band"></div>
  </section>

</div>
</body>
</html>
```